Sandwich Board and Poster design promoting a medical aesthetic clinic

I am looking for a clean, modern and relaxing design promoting a medical physician-led aesthetic clinic.
Services offered are neuromodulator treatment (Dyneline) and Dermal Fillers.
Logo must be included.
Use the tag line "Refresh your look, revive your spirit."
Address is 204-205 27361 93 Ave, Surrey, K7P 2R4
604-555-0172
email - info@brightmoorskin.ca
www.brightmoorskin.ca

```html
<!DOCTYPE html>
<html lang="en">
<head>
<meta charset="utf-8">
<title>Brightmoor Renewal – Poster</title>
<link rel="stylesheet" href="https://fonts.googleapis.com/css2?family=Montserrat:wght@500&family=Cormorant+Garamond:wght@400&family=Great+Vibes&family=Arimo:wght@400;700&display=swap">
<style>
  :root {
    --backdrop: #8c7770;
    --paper-top: #f4f1e8;
    --paper-bottom: #eeeadf;
    --ink: #141414;
    --taupe: #86746e;
    --taupe-text: #7a6862;
    --phone-grey: #8f7f7a;
    --black-band: #050505;
    --white: #ffffff;
    --photo-light: #f7f6f4;
    --photo-skin: #d9b7a0;
    --photo-dark: #3a2a24;
  }
  * { margin: 0; padding: 0; box-sizing: border-box; }
  html, body {
    width: 1200px; height: 840px; overflow: hidden;
    background: var(--backdrop);
  }
  .poster {
    position: absolute;
    left: 323px; top: 30px;
    width: 554px; height: 780px;
    background: linear-gradient(180deg, var(--paper-top), var(--paper-bottom));
    overflow: hidden;
  }
  .poster__photo {
    position: absolute; left: 0; top: 0;
    width: 100%; height: 320px;
    background: linear-gradient(90deg,
      var(--photo-dark) 0%, var(--photo-skin) 12%, var(--photo-skin) 36%,
      var(--photo-light) 44%, var(--photo-light) 62%,
      var(--photo-skin) 70%, #8a5a42 86%, var(--photo-dark) 100%);
  }
  .brand {
    position: absolute; left: 0; top: 340px; width: 100%;
    text-align: center;
    font-family: 'Montserrat', sans-serif; font-weight: 500;
    color: var(--ink);
  }
  .brand__name {
    font-size: 34px; letter-spacing: 10px; line-height: 1;
    padding-left: 10px;
  }
  .brand__sub {
    margin-top: 8px;
    font-size: 12px; letter-spacing: 7px; line-height: 1;
    padding-left: 7px;
  }
  .tagline {
    position: absolute; left: 0; top: 0; width: 100%; height: 100%;
    color: var(--taupe-text);
  }
  .tagline__plain {
    position: absolute;
    font-family: 'Cormorant Garamond', serif;
    font-size: 19px; letter-spacing: 0.5px; text-transform: uppercase;
  }
  .tagline__script {
    position: absolute;
    font-family: 'Great Vibes', cursive;
    font-size: 74px; line-height: 1;
  }
  .tagline__plain--one { left: 102px; top: 462px; }
  .tagline__script--look { left: 236px; top: 432px; }
  .tagline__plain--two { left: 208px; top: 504px; }
  .tagline__script--spirit { left: 330px; top: 476px; }
  .services {
    position: absolute; left: 60px; top: 584px;
    width: 438px; height: 59px;
    background: var(--taupe);
    color: var(--white);
    font-family: 'Arimo', sans-serif; font-weight: 700;
    font-size: 14px; line-height: 21px;
    text-align: center;
    padding-top: 9px;
  }
  .contact {
    position: absolute; left: 60px; top: 643px;
    width: 438px; height: 82px;
    background: var(--black-band);
    text-align: center;
    font-family: 'Arimo', sans-serif;
  }
  .contact__address {
    color: var(--white); font-weight: 700;
    font-size: 11px; margin-top: 9px; letter-spacing: 0.2px;
  }
  .contact__phone {
    color: var(--phone-grey); font-weight: 700;
    font-size: 27px; letter-spacing: 4px; line-height: 1;
    margin-top: 6px;
  }
  .contact__links {
    display: flex; justify-content: center; gap: 8px;
    color: var(--white); font-size: 9px; letter-spacing: 0.6px;
    margin-top: 6px;
  }
  .contact__link { display: flex; align-items: center; gap: 3px; }
  .contact__link svg { width: 7px; height: 7px; }
</style>
</head>
<body>
  <main class="poster">
    <div class="poster__photo" role="img" aria-label="Photograph of four women in profile, two on each side facing each other, against a white background"></div>

    <div class="brand">
      <div class="brand__name">BRIGHTMOOR</div>
      <div class="brand__sub">RENEWAL</div>
    </div>

    <div class="tagline">
      <span class="tagline__plain tagline__plain--one">Refresh your</span>
      <span class="tagline__script tagline__script--look">Look</span>
      <span class="tagline__plain tagline__plain--two">Revive your</span>
      <span class="tagline__script tagline__script--spirit">Spirit</span>
    </div>

    <div class="services">
      NEUROMODULATOR TREATMENT (DYNELINE)"<br>AND "DERMAL FILLERS.
    </div>

    <div class="contact">
      <div class="contact__address">204-205 27361 93 AVE, SURREY, K7P 2R4</div>
      <div class="contact__phone">604-555-0172</div>
      <div class="contact__links">
        <span class="contact__link">
          <svg viewBox="0 0 10 10"><circle cx="5" cy="5" r="4.2" fill="none" stroke="#fff" stroke-width="1.2"/></svg>
          info@brightmoorskin.ca
        </span>
        <span class="contact__link">
          <svg viewBox="0 0 10 10"><circle cx="5" cy="5" r="4.2" fill="none" stroke="#fff" stroke-width="1.2"/><line x1="1" y1="5" x2="9" y2="5" stroke="#fff" stroke-width="0.8"/></svg>
          www.brightmoorskin.ca
        </span>
      </div>
    </div>
  </main>
</body>
</html>
```